BRISK requires an exciting new business card

New business card required for BRISK. We are a new market research consultancy and want our brand to be approachable and be contemporary/modern, bold, uncomplicated/simple, and use friendly and easy to read fonts.

A draft website front page is attached to give you a feel (the pictures will be improved over the coming days).

The business card will be printed on 600gsm card, full colour both sides. The card is unique in that it allows one of four colours to be placed within the seam of the card (see http://uk.prentvo.com/products/gilt/business-cards.html)

The logo has been designed in yellow on white, white on yellow, yellow on black and black on yellow - please select whichever you feel most appropriate from the attached document (please use the versions with the tagline). I think my preference is yellow on white for the front, and then yellow or black as the dominant colour on the back.

Telephone numbers will be given next week as they are now being finalised.

Thanks

Target Market(s)

Professionals in large corporates, such as Marketing Managers at Grovane, Fizzaro Pop, Delmarco etc.

Industry/Entity Type

Market Research

Requirements
Must have
• Dana Pruitt QPMR
brisk
Level 4, 37 Quarrell St
Surrey Hills
NSW 2010
Tel: 02 XXXX XXXX
Mob: XXXX XXXXXX
Email: dana@briskqr.com.au
Web: www.briskqr.com.au

```html
<!DOCTYPE html>
<html lang="en">
<head>
<meta charset="utf-8">
<title>BRISK business card</title>
<link rel="stylesheet" href="https://fonts.googleapis.com/css2?family=Open+Sans:wght@400;600;700;800&display=swap">
<style>
  :root {
    --brand-yellow: #ffcc00;
    --pale-yellow: #fff5cc;
    --ink: #3a3a3a;
    --soft-ink: #555555;
    --faint-grey: #ededed;
    --card-white: #ffffff;
    --backdrop: #e4e4ea;
  }
  * { box-sizing: border-box; margin: 0; padding: 0; }
  html, body {
    width: 1200px; height: 987px; overflow: hidden;
    background: var(--backdrop);
    font-family: "Open Sans", Arial, sans-serif;
    color: var(--ink);
  }
  .canvas { position: relative; width: 1200px; height: 987px; }
  .card {
    position: absolute; width: 720px; height: 440px;
    background: var(--card-white); border-radius: 36px; overflow: hidden;
    box-shadow: 0 10px 30px rgba(0,0,0,0.12);
  }
  .card--back { left: 440px; top: 30px; }
  .card--front { left: 40px; top: 517px; }

  .brand-name {
    font-weight: 800; color: var(--brand-yellow);
    line-height: 1; letter-spacing: -2px;
  }
  .tagline { color: var(--soft-ink); font-weight: 400; }

  /* back */
  .back-disc {
    position: absolute; left: 250px; top: 40px; width: 330px; height: 330px;
    border-radius: 50%; background: var(--faint-grey);
  }
  .back-logo { position: absolute; left: 120px; top: 95px; }
  .back-logo .brand-name { font-size: 170px; }
  .back-logo .tagline { font-size: 34px; margin-top: 2px; margin-left: 10px; }
  .back-url {
    position: absolute; left: 130px; top: 330px;
    font-size: 22px; letter-spacing: 7px; color: var(--ink);
  }

  /* front */
  .front-logo { position: absolute; left: 60px; top: 36px; }
  .front-logo .brand-name { font-size: 120px; }
  .front-tagline { position: absolute; left: 70px; top: 160px; font-size: 25px; }
  .contact-list { position: absolute; left: 60px; top: 210px; list-style: none; }
  .contact-list li {
    display: flex; align-items: center; gap: 10px;
    font-size: 18px; line-height: 30px; color: var(--ink);
  }
  .contact-icon { width: 18px; height: 18px; flex: none; }
  .name-disc {
    position: absolute; left: 470px; top: 245px; width: 150px; height: 150px;
    border-radius: 50%; background: var(--pale-yellow);
  }
  .holder { position: absolute; right: 50px; top: 300px; font-size: 26px; }
  .holder strong { font-weight: 700; }
  .holder span { font-weight: 400; }
  .address-band {
    position: absolute; left: 0; bottom: 0; width: 100%; height: 58px;
    background: var(--brand-yellow);
    display: flex; align-items: center; padding-left: 60px;
    font-size: 20px; font-weight: 600; color: var(--ink);
  }
</style>
</head>
<body>
<main class="canvas">

  <section class="card card--back" aria-label="Card back">
    <div class="back-disc"></div>
    <div class="back-logo">
      <div class="brand-name">brisk</div>
      <div class="tagline">insight made simple</div>
    </div>
    <div class="back-url">www.briskqr.com.au</div>
  </section>

  <section class="card card--front" aria-label="Card front">
    <div class="front-logo">
      <div class="brand-name">brisk</div>
    </div>
    <div class="tagline front-tagline">insight made simple</div>

    <ul class="contact-list">
      <li>
        <svg class="contact-icon" viewBox="0 0 18 18"><circle cx="9" cy="9" r="9" fill="#ffcc00"/><path d="M6 4.5c-1 1-1 3 1 5.5s4.5 3 5.5 2l-1.5-1.8-1.3.6c-1-.6-2-1.7-2.4-2.6l.7-1.2z" fill="#fff"/></svg>
        02 5550 1847
      </li>
      <li>
        <svg class="contact-icon" viewBox="0 0 18 18"><circle cx="9" cy="9" r="9" fill="#ffcc00"/><rect x="6" y="3.5" width="6" height="11" rx="1.2" fill="#fff"/><rect x="7" y="5" width="4" height="6" fill="#ffcc00"/></svg>
        0455 501 932
      </li>
      <li>
        <svg class="contact-icon" viewBox="0 0 18 18"><circle cx="9" cy="9" r="9" fill="#ffcc00"/><rect x="4" y="5.5" width="10" height="7" rx="1" fill="#fff"/><path d="M4.5 6l4.5 3.5L13.5 6" stroke="#ffcc00" stroke-width="1" fill="none"/></svg>
        dana@briskqr.com.au
      </li>
      <li>
        <svg class="contact-icon" viewBox="0 0 18 18"><circle cx="9" cy="9" r="9" fill="#ffcc00"/><circle cx="9" cy="9" r="5" fill="none" stroke="#fff" stroke-width="1.2"/><ellipse cx="9" cy="9" rx="2.2" ry="5" fill="none" stroke="#fff" stroke-width="1"/><line x1="4" y1="9" x2="14" y2="9" stroke="#fff" stroke-width="1"/></svg>
        www.briskqr.com.au
      </li>
    </ul>

    <div class="name-disc"></div>
    <p class="holder"><strong>Dana Pruitt</strong> <span>QPMR</span></p>

    <div class="address-band">Level 4, 37 Quarrell St, Alder Vale, NSW 2301</div>
  </section>

</main>
</body>
</html>
```